Brintel Works - Fast, Efficient and Gas Mainteance for Domestic, Commercial and Industrial clients

We are in the process of purchasing a new business and would like to get a new logo and business card.
Business is a gas maintenance business that also does new gas installations.
Has been established since 1988.
Services include:
Install all types of gas appliances & equipment inc. hot water units
Maintain / repair / replace all types of gas appliances & equipment

Target Market(s)

Domestic, Commercial and Industrial clients

Industry/Entity Type

Business

Contact Information for Business Card

admin@brintelworks.com.au
07 3918 4726
Brintel Works PTY LTD

Logo Text

Gas Fitting & Plumbing Maintenance Specialists

Font styles to use
Sans Serif

Requirements
Must have
• Logo
• Business name, contact number, email address, web address
• Domestic | Commercial | Industrial Est Since 1988
Nice to have
• Possibly a black card with a flame logo to one side
Should not have
• Spelling errors

```html
<!DOCTYPE html>
<html lang="en">
<head>
<meta charset="utf-8">
<title>Brintel Works – Business Card</title>
<link rel="stylesheet" href="https://fonts.googleapis.com/css2?family=Source+Sans+3:wght@400;600&display=swap">
<style>
  :root {
    --backdrop: #2b2725;
    --card: #0c0c0c;
    --card-edge: #1a1a1a;
    --text: #e9e9e9;
    --text-soft: #cfcfcf;
    --accent: #f08a1c;
    --accent-warm: #e8392a;
    --divider: #6a4a22;
    --silver: #d8d8d8;
  }
  * { margin: 0; padding: 0; box-sizing: border-box; }
  html, body { width: 1200px; height: 900px; overflow: hidden; }
  body {
    background: var(--backdrop);
    font-family: "Source Sans 3", "Myriad Pro", Arial, sans-serif;
    position: relative;
  }
  .card {
    position: absolute;
    top: 300px;
    width: 520px;
    height: 300px;
    background: var(--card);
    border: 1px solid var(--card-edge);
    box-shadow: 0 14px 30px rgba(0,0,0,0.55);
  }
  .card--details { left: 50px; }
  .card--brand { left: 630px; }

  /* Details side */
  .brand-block {
    position: absolute;
    left: 34px;
    top: 86px;
    width: 170px;
    display: flex;
    align-items: center;
    gap: 10px;
  }
  .brand-block__dot {
    width: 14px; height: 14px;
    border-radius: 50%;
    background: var(--accent);
    flex: none;
  }
  .brand-block__name {
    color: var(--accent);
    font-weight: 600;
    font-size: 26px;
    line-height: 1.1;
  }
  .divider {
    position: absolute;
    left: 232px;
    top: 60px;
    width: 1px;
    height: 120px;
    background: linear-gradient(to bottom, transparent, var(--divider), transparent);
  }
  .contact {
    position: absolute;
    left: 252px;
    top: 52px;
    color: var(--text);
    font-size: 14.5px;
    line-height: 1.25;
  }
  .contact__address { margin-bottom: 14px; }
  .contact__list { list-style: none; }
  .contact__item { display: flex; align-items: center; gap: 8px; }
  .contact__icon { width: 11px; height: 11px; flex: none; }
  .tagline {
    position: absolute;
    left: 0; right: 0;
    bottom: 40px;
    text-align: center;
    color: var(--text);
    font-size: 17px;
    letter-spacing: 0.2px;
  }

  /* Brand side */
  .brand-face {
    position: absolute;
    inset: 0;
    display: flex;
    align-items: center;
    justify-content: center;
    gap: 12px;
  }
  .brand-face__mark {
    width: 16px; height: 16px;
    border: 0;
    border-radius: 50%;
    background: var(--silver);
  }
  .brand-face__name {
    color: var(--silver);
    font-weight: 600;
    font-size: 30px;
  }
</style>
</head>
<body>

<section class="card card--details" aria-label="Business card, contact side">
  <div class="brand-block">
    <span class="brand-block__dot"></span>
    <span class="brand-block__name">Brintel Works</span>
  </div>
  <div class="divider"></div>
  <div class="contact">
    <p class="contact__address">12345, Address Goes Here<br>Country Name, 123456.</p>
    <ul class="contact__list">
      <li class="contact__item">
        <svg class="contact__icon" viewBox="0 0 12 12"><path d="M2.5 1l2 2-1 1.5c.8 1.6 2 2.8 3.5 3.5L8.5 7l2 2-1.5 2C5 10.5 1.5 7 1 3z" fill="var(--accent)"/></svg>
        07 3918 4726
      </li>
      <li class="contact__item">
        <svg class="contact__icon" viewBox="0 0 12 12"><rect x="1" y="2.5" width="10" height="7" fill="var(--accent)"/><path d="M1 2.5l5 4 5-4" fill="none" stroke="#5a2a00" stroke-width="1"/></svg>
        admin@brintelworks.com.au
      </li>
      <li class="contact__item">
        <svg class="contact__icon" viewBox="0 0 12 12"><circle cx="6" cy="6" r="5" fill="var(--accent)"/><path d="M1 6h10M6 1c-2.5 3-2.5 7 0 10M6 1c2.5 3 2.5 7 0 10" fill="none" stroke="#5a2a00" stroke-width="0.8"/></svg>
        www.brintelworks.com.au
      </li>
    </ul>
  </div>
  <p class="tagline">Domestic | Commercial | Industrial Est Since 1988</p>
</section>

<section class="card card--brand" aria-label="Business card, brand side">
  <div class="brand-face">
    <span class="brand-face__mark"></span>
    <span class="brand-face__name">Brintel Works PTY LTD</span>
  </div>
</section>

</body>
</html>
```